I need a design that promotes "A peak path hub for runners". services include assessment, massage, physiotherapy, pilates, suspension training, kinesiotaping in any combination.
I would like to bring the design into my website, flyers etc

Target Market(s)

athletes from beginner to elite - any age, male and female

Industry/Entity Type

Shop

Contact Information for Business Card

Peak-Path Hub for Runners
17 Corla Lane, Westmere, Tauranga
021 874 3061
tess.harlow@mailbrook.example

Logo Text

Logo styles of interest
Abstract Logo
Requirements
Nice to have
• Blue colour theme

```html
<!DOCTYPE html>
<html lang="en">
<head>
<meta charset="utf-8">
<title>Peak-Path Hub for Runners – Business Card</title>
<link href="https://fonts.googleapis.com/css2?family=Oswald:wght@700&family=Open+Sans:wght@400&display=swap" rel="stylesheet">
<style>
  :root {
    --navy: #1b1d4d;
    --sky: #1e9bd7;
    --white: #ffffff;
    --backdrop: #e9ebf0;
  }
  * { box-sizing: border-box; margin: 0; padding: 0; }
  html, body {
    width: 1200px;
    height: 1000px;
    overflow: hidden;
    background: var(--backdrop);
    font-family: "Open Sans", sans-serif;
  }
  .card {
    position: absolute;
    left: 200px;
    width: 800px;
    height: 460px;
    background: var(--navy);
    border-radius: 28px;
    overflow: hidden;
  }
  .card--front { top: 20px; }
  .card--back { top: 515px; }

  /* Front */
  .top-rule {
    position: absolute;
    left: 0; right: 0; top: 58px;
    height: 6px;
    background: var(--sky);
  }
  .brand {
    position: absolute;
    left: 120px; top: 140px;
    display: flex;
    align-items: center;
    gap: 16px;
  }
  .brand__dot {
    width: 62px; height: 62px;
    border-radius: 50%;
    background: var(--sky);
  }
  .brand__name {
    font-family: "Oswald", sans-serif;
    font-weight: 700;
    font-size: 46px;
    letter-spacing: 0.5px;
    color: var(--sky);
    text-transform: uppercase;
  }
  .address {
    position: absolute;
    left: 360px; top: 225px;
    font-size: 23px;
    line-height: 31px;
    color: var(--sky);
  }
  .contact-band {
    position: absolute;
    left: 0; right: 0; top: 335px;
    height: 58px;
    background: var(--sky);
    display: flex;
    justify-content: space-between;
    align-items: center;
    padding: 0 56px 0 80px;
    color: var(--white);
    font-size: 23px;
  }

  /* Back */
  .hero-circle {
    position: absolute;
    left: 0; top: 0;
  }
  .services {
    position: absolute;
    left: 470px; top: 72px;
    display: flex;
    gap: 22px;
  }
  .services__label {
    display: flex;
    flex-direction: column;
    color: var(--white);
    font-size: 26px;
    line-height: 37px;
    text-align: center;
    width: 24px;
  }
  .services__divider {
    width: 3px;
    background: var(--sky);
  }
  .services__list {
    list-style: none;
    color: var(--sky);
    font-size: 26px;
    line-height: 42px;
    letter-spacing: -0.5px;
  }
</style>
</head>
<body>

<section class="card card--front" aria-label="Business card front">
  <div class="top-rule"></div>
  <div class="brand">
    <span class="brand__dot"></span>
    <span class="brand__name">Peak-Path Hub for Runners</span>
  </div>
  <p class="address">17 Corla Lane,<br>Westmere,<br>Tauranga</p>
  <div class="contact-band">
    <span class="contact-band__phone">Phone 021 874 3061</span>
    <span class="contact-band__email">tess.harlow@mailbrook.example</span>
  </div>
</section>

<section class="card card--back" aria-label="Business card back">
  <svg class="hero-circle" width="800" height="460" viewBox="0 0 800 460" role="img" aria-label="Large sky-blue circle where the running athlete illustration belongs">
    <circle cx="150" cy="230" r="280" fill="var(--sky)"/>
  </svg>
  <div class="services">
    <div class="services__label" aria-label="services">
      <span>s</span><span>e</span><span>r</span><span>v</span><span>i</span><span>c</span><span>e</span><span>s</span>
    </div>
    <div class="services__divider"></div>
    <ul class="services__list">
      <li>Assessment</li>
      <li>Massage</li>
      <li>Physiotherapy</li>
      <li>Pilates</li>
      <li>Suspension training</li>
      <li>Kinesiotaping</li>
      <li>in any combination.</li>
    </ul>
  </div>
</section>

</body>
</html>
```